Bench Advertisement - We Buy Houses Design Needed

Need a catchy, simple but elegant design for bus benches to advertise our company.

We need our website, or phone number, and a smal description (1-2 bulletpoints of what we do and what we offer)

The tricky part is for the designer to fit everything and make the website name as part of the title and fitting everything so that people passing by on the street can see what we offer.

Our website is quickdealhomebuyer.com - (916) 555-0143

Something simple but something that catches the eye of walking pedestrians, and drivers driving by the bench.

Our company buys houses, any condition, any situation, we buy houses for cash and close quickly. You can use this description to create a few bulletpoints however you like. Must follow dimensions in attachment.

Target Market(s)

People in foreclosure, about to lose their homes, people that need a quick cash sale of their property

Industry/Entity Type

Real Estate

Requirements
Must have
• catchy, website name, phone number, few brief bulletpoints about what we offer, colors that will catch peoples eye while walking or driving - advertisement will be placed on bus benches - visit our website to see the type of houses we buy - Also have more work for winner of design with possible bonuses
Nice to have
• Feel free to use description or images on our website - make sure the description is just bullet points and it fits with the overall theme / size of the advertisement - Bold bright colors - put yourself in their shoes (if you were going through financial difficulties and about to lose your house to foreclosure or auction, what would you want to see to pick up the phone and call us for a quick sale of your house?) (or if you have a house that you are having a problem with, problem renters, unkept/beat up house, what would make you want to call us and sell your house to us?)

```html
<!DOCTYPE html>
<html lang="en">
<head>
<meta charset="utf-8">
<title>Quick Deal Home Buyer – Bench Advertisement</title>
<link rel="stylesheet" href="https://fonts.googleapis.com/css2?family=Ubuntu:wght@300;400;500&display=swap">
<style>
  :root {
    --page-bg: #e9e6e1;
    --frame-silver: #dcdad6;
    --frame-red: #d8342a;
    --photo-sky: #b9c3c8;
    --photo-wood: #a5674a;
    --photo-wall: #b8b2a8;
    --photo-tarp: #2f6cc0;
    --photo-siding: #94553c;
    --photo-green: #4f7a45;
    --photo-ground: #4a4640;
    --text-white: #ffffff;
  }
  * { box-sizing: border-box; margin: 0; padding: 0; }
  html, body {
    width: 1200px;
    height: 606px;
    overflow: hidden;
    background: var(--page-bg);
    font-family: "Ubuntu", sans-serif;
  }
  .canvas {
    position: relative;
    width: 1200px;
    height: 606px;
  }
  .bench-ad {
    position: absolute;
    left: 40px;
    top: 150px;
    width: 1120px;
    height: 306px;
    background: var(--frame-silver);
    padding: 5px;
    box-shadow: 0 2px 6px rgba(0,0,0,0.25);
  }
  .bench-ad__inner {
    position: relative;
    width: 100%;
    height: 100%;
    border: 4px solid var(--frame-red);
    overflow: hidden;
  }
  .bench-ad__photo {
    position: absolute;
    inset: 0;
    background:
      linear-gradient(180deg, rgba(30,30,35,0.15) 0%, rgba(30,30,35,0.1) 40%, rgba(20,20,20,0.4) 100%),
      linear-gradient(180deg, rgba(190,200,205,0.55) 0%, rgba(190,200,205,0) 18%),
      linear-gradient(90deg,
        var(--photo-wood) 0%, var(--photo-wood) 20%,
        var(--photo-wall) 23%, var(--photo-wall) 48%,
        var(--photo-tarp) 50%, var(--photo-tarp) 70%,
        var(--photo-siding) 73%, var(--photo-siding) 84%,
        var(--photo-green) 90%, var(--photo-green) 100%);
  }
  .brand {
    position: absolute;
    left: 74px;
    top: 30px;
    display: flex;
    flex-direction: column;
    align-items: center;
    gap: 10px;
  }
  .brand__mark {
    width: 22px;
    height: 22px;
    background: var(--text-white);
  }
  .brand__name {
    color: var(--text-white);
    font-size: 16px;
    font-weight: 400;
    letter-spacing: 0.2px;
    text-transform: uppercase;
    text-shadow: 0 1px 3px rgba(0,0,0,0.5);
  }
  .call-line {
    position: absolute;
    right: 24px;
    top: 26px;
    color: var(--text-white);
    font-size: 32px;
    font-weight: 400;
    text-shadow: 0 1px 3px rgba(0,0,0,0.5);
  }
  .headline {
    position: absolute;
    left: 0;
    right: 0;
    top: 145px;
    text-align: center;
    color: var(--text-white);
    font-size: 58px;
    font-weight: 400;
    line-height: 1;
    letter-spacing: -0.3px;
    text-shadow: 0 2px 4px rgba(0,0,0,0.5);
  }
  .offer {
    position: absolute;
    left: 0;
    right: 0;
    top: 218px;
    text-align: center;
    color: var(--text-white);
    font-size: 25px;
    font-weight: 300;
    line-height: 1.2;
    text-shadow: 0 1px 3px rgba(0,0,0,0.6);
  }
</style>
</head>
<body>
<main class="canvas">
  <section class="bench-ad">
    <div class="bench-ad__inner">
      <div class="bench-ad__photo" role="img" aria-label="Photo of a run-down house with boarded windows, a blue tarp and piled debris in the yard"></div>
      <div class="brand">
        <span class="brand__mark" aria-hidden="true"></span>
        <span class="brand__name">Quick Deal Home Buyer</span>
      </div>
      <p class="call-line">Call now : (916) 555-0143</p>
      <h1 class="headline">Visit now: quickdealhomebuyer.com</h1>
      <p class="offer">Our company buys houses, any condition, any situation,<br>we buy houses for cash and close quickly.</p>
    </div>
  </section>
</main>
</body>
</html>
```